Velmor Spire Nine Flash website

we need a website to cater to 2 aspect of the business. We have Velmor spire residence and velmor spire office. For the office, we will get their inquire and arrange a face to face meetup to show them the office area for rent. For the residence side, it will need to be like staylane or roomvio.com. we want to allow them to book online for the date they need. We have a total of 10 different room configurations starting at $70 per night and up depending on the size of the room. example of the design is https://brisquelodge.com/

Target Market(s)

the website should have detail information on the layout, designs, and luxury of the building.

Industry/Entity Type

office and service appartment rental/lease

Coding

Coded - Design and coding required

Number of Pages Required

5+ page

Requirements
Must have
• a luxury perspective
Nice to have
• example https://brisquelodge.com/

```html
<!DOCTYPE html>
<html lang="en">
<head>
<meta charset="utf-8">
<title>Velmor Spire Nine – Landing Page Mobile View</title>
<link href="https://fonts.googleapis.com/css2?family=Montserrat:wght@400;600;700&family=Poppins:wght@300;400;500;600&display=swap" rel="stylesheet">
<style>
  :root{
    --gold:#D4A02A;
    --gold-soft:#E5C98F;
    --board:#EEDDB9;
    --cream:#FBF5E8;
    --ink:#2B2B2B;
    --muted:#777;
    --line:#E4E4E4;
    --white:#FFFFFF;
    --slate:#6E6E6E;
    --mark:#4A4A4A;
  }
  *{box-sizing:border-box;margin:0;padding:0}
  html,body{width:1200px;height:771px;overflow:hidden}
  body{background:var(--board);font-family:'Poppins',sans-serif;color:var(--ink);position:relative}

  .intro{position:absolute;left:0;top:0;width:247px;height:771px;background:var(--white)}
  .intro__title{position:absolute;left:44px;top:155px;font-family:'Montserrat',sans-serif;font-weight:700;font-size:27px;line-height:1.15;color:var(--gold)}
  .intro__sub{position:absolute;left:44px;top:232px;font-weight:300;font-size:19px;line-height:1.4;color:var(--ink)}
  .intro__block{position:absolute;left:0;top:448px;width:247px;height:323px;background:var(--gold);border-top-right-radius:18px}
  .intro__mark{position:absolute;left:86px;top:410px;width:58px;height:64px;background:var(--mark)}

  .screen{position:absolute;background:var(--white);overflow:hidden}
  .footer-screen{left:288px;top:0;width:250px;height:314px;border-radius:0 0 22px 22px;padding:0 24px}
  .hero-screen{left:288px;top:339px;width:250px;height:432px;border-radius:22px 22px 0 0}
  .residence-screen{left:595px;top:0;width:265px;height:771px}
  .faq-screen{left:905px;top:0;width:263px;height:771px}

  .f-phone{font-size:7px;color:var(--muted);margin-top:-3px}
  .f-head{font-family:'Montserrat',sans-serif;font-weight:700;font-size:10px;color:var(--gold);margin:9px 0 4px}
  .f-link{font-size:8px;color:var(--muted);line-height:1.55}
  .f-input{margin-top:8px;height:20px;border:1px solid var(--line);border-radius:4px;font-size:7px;color:#aaa;padding:5px 8px}
  .f-btn{margin-top:7px;height:18px;border:1px solid var(--gold);border-radius:10px;font-size:7px;color:var(--gold);text-align:center;line-height:16px}
  .f-social{display:flex;gap:6px;margin-top:12px}
  .f-social span{width:17px;height:17px;border:1px solid var(--gold);border-radius:50%}
  .f-rule{height:1px;background:var(--line);margin:10px 0 8px}
  .f-copy{font-size:7px;color:var(--muted);text-align:center}
  .f-copy b{color:var(--gold);font-weight:500}

  .topbar{height:44px;display:flex;align-items:center;justify-content:space-between;padding:0 16px}
  .brand{display:flex;align-items:center;gap:5px;font-family:'Montserrat',sans-serif;font-weight:600;font-size:8px;color:var(--gold)}
  .brand i{width:9px;height:9px;border:1px solid var(--gold)}
  .burger{width:18px;display:grid;gap:3px}
  .burger span{height:2px;background:var(--gold)}
  .hero-media{position:absolute;left:0;top:44px;width:250px;height:388px;background:linear-gradient(160deg,#B99872 0%,#8A6A4E 45%,#3C3029 100%)}
  .play{position:absolute;left:100px;top:110px}
  .hero-caption{position:absolute;left:0;bottom:0;width:100%;padding:40px 20px 14px;background:linear-gradient(transparent,rgba(0,0,0,.65));color:var(--white);font-weight:600;font-size:9.5px;text-align:center;line-height:1.35}

  .sec-title{font-family:'Montserrat',sans-serif;font-weight:700;font-size:18px;color:var(--gold);text-align:center;padding-top:40px;white-space:nowrap}
  .sec-title span{font-weight:400;color:var(--gold-soft)}
  .title-rule{width:90px;height:2px;background:var(--gold-soft);margin:10px auto 14px}
  .lead{font-size:12.5px;font-weight:300;color:#555;text-align:center;line-height:1.45;padding:0 14px}
  .banner{position:relative;margin-top:30px;height:66px}
  .banner svg{position:absolute;left:0;top:0}
  .banner p{position:absolute;left:6px;top:10px;width:215px;font-size:12.5px;color:var(--white);line-height:1.4}
  .room-media{position:absolute;left:0;top:315px;width:265px;height:210px;background:linear-gradient(135deg,#CFCAC4 0%,#9C958D 50%,#4A4541 100%)}
  .room-label{position:absolute;left:6px;bottom:18px;color:var(--white);font-family:'Montserrat',sans-serif;font-weight:600;font-size:14px}
  .room-meta{position:absolute;left:6px;bottom:4px;color:var(--white);font-size:10px;display:flex;align-items:center;gap:4px}
  .pager{position:absolute;left:0;top:540px;width:265px;display:flex;gap:4px;justify-content:center}
  .pager span{width:18px;height:3px;background:#C9C9C9}
  .pager span.on{background:#6C6C6C}
  .learn{position:absolute;left:40px;top:570px;width:185px;height:22px;border-top:1px solid var(--gold-soft);border-bottom:1px solid var(--gold-soft);font-size:8px;color:var(--gold);text-align:center;line-height:20px}
  .office{position:absolute;left:0;top:645px;width:265px;height:126px;background:var(--cream)}
  .office .sec-title{padding-top:32px;font-size:17px}
  .office .lead{margin-top:26px;font-size:12px}

  .book-btn{width:200px;height:24px;margin:0 auto;background:var(--gold);border-radius:0 0 12px 12px;font-size:8px;color:var(--white);text-align:center;line-height:24px}
  .faq-title{font-family:'Montserrat',sans-serif;font-weight:700;font-size:17px;line-height:1.25;color:var(--gold);padding:50px 12px 0}
  .faq-intro{font-size:7.5px;color:var(--muted);padding:8px 12px 0;line-height:1.5}
  .faq-btn{margin:14px 12px 0;height:16px;background:var(--gold);border-radius:9px;font-size:6.5px;color:var(--white);text-align:center;line-height:16px}
  .faq-list{margin:20px 12px 0}
  .faq-item{border-bottom:1px solid var(--line);padding:8px 0 7px;position:relative}
  .faq-q{font-size:7.5px;color:var(--gold);font-weight:500;line-height:1.4;padding-right:22px}
  .faq-a{font-size:6.5px;color:var(--muted);line-height:1.5;margin-top:5px}
  .faq-item svg{position:absolute;right:0;top:10px}
  .connect{position:absolute;left:0;top:500px;width:263px;height:271px;background:linear-gradient(150deg,#8C7A66 0%,#5A4B3E 50%,#2E2824 100%);padding:20px 16px;text-align:center;color:var(--white)}
  .connect h2{font-family:'Montserrat',sans-serif;font-weight:700;font-size:15px;color:var(--gold)}
  .connect p{font-size:8px;line-height:1.55;margin-top:6px}
  .connect .cta{margin:20px auto 0;width:210px;height:16px;background:var(--gold);border-radius:9px;font-size:6.5px;line-height:16px}
</style>
</head>
<body>
  <section class="intro">
    <h1 class="intro__title">Velmor Spire<br>Nine</h1>
    <p class="intro__sub">Landing Page<br>Mobile View</p>
    <div class="intro__block"></div>
    <div class="intro__mark"></div>
  </section>

  <section class="screen footer-screen">
    <p class="f-phone">+00 123 456 7890</p>
    <h3 class="f-head">Project</h3>
    <p class="f-link">Studio</p>
    <p class="f-link">Bed room</p>
    <h3 class="f-head">Quick Links</h3>
    <p class="f-link">About Us</p>
    <p class="f-link">Services</p>
    <p class="f-link">Privacy Policy</p>
    <p class="f-link">Terms &amp; Conditions</p>
    <h3 class="f-head">Your Gateway to Exclusive Updates!</h3>
    <div class="f-input">Enter your email...</div>
    <div class="f-btn">Subscribe</div>
    <div class="f-social"><span></span><span></span><span></span></div>
    <div class="f-rule"></div>
    <p class="f-copy">© 2024 <b>Velmor Spire Nine</b>. All Rights Reserved.</p>
  </section>

  <section class="screen hero-screen">
    <header class="topbar">
      <div class="brand"><i></i>Velmor Spire Nine</div>
      <div class="burger"><span></span><span></span><span></span></div>
    </header>
    <div class="hero-media" role="img" aria-label="Video still of a couple relaxing together in a warm-toned apartment">
      <svg class="play" width="50" height="50" viewBox="0 0 50 50"><circle cx="25" cy="25" r="23" fill="none" stroke="#fff" stroke-width="2"/><path d="M20 15 L35 25 L20 35 Z" fill="#fff"/></svg>
      <p class="hero-caption">Experience the perfect blend of luxury and functionality at Velmor Spire Nine</p>
    </div>
  </section>

  <section class="screen residence-screen">
    <h2 class="sec-title">Velmor Spire <span>Residences</span></h2>
    <div class="title-rule"></div>
    <p class="lead">Indulge in luxurious living at Velmor Spire Residences, find the perfect space for your lifestyle.</p>
    <div class="banner">
      <svg width="265" height="66" viewBox="0 0 265 66"><path d="M0 0 H232 L262 33 L232 66 H0 Z" fill="#6E6E6E"/></svg>
      <p>With <b><i>10 unique room</i></b> configurations starting at <b>$70</b> per night.</p>
    </div>
    <div class="room-media" role="img" aria-label="Studio room interior with a person, a bed and a potted plant">
      <p class="room-label">Type A, Studio</p>
      <p class="room-meta">
        <svg width="9" height="9" viewBox="0 0 10 10"><circle cx="5" cy="3" r="2.2" fill="#fff"/><path d="M1 10 C1 6 9 6 9 10 Z" fill="#fff"/></svg>2
        &nbsp;
        <svg width="9" height="9" viewBox="0 0 10 10"><rect x="1" y="1" width="8" height="8" fill="none" stroke="#fff" stroke-width="1.2"/></svg>38.75
      </p>
    </div>
    <div class="pager"><span></span><span></span><span class="on"></span><span></span><span></span><span></span><span></span></div>
    <div class="learn">Learn More</div>
    <div class="office">
      <h2 class="sec-title">Velmor Spire <span>Office Space</span></h2>
      <p class="lead">Explore our state-of-the-art office</p>
    </div>
  </section>

  <section class="screen faq-screen">
    <div class="book-btn">Book Now</div>
    <h2 class="faq-title">Frequently Asked Questions About Velmor Spire Nine</h2>
    <p class="faq-intro">Find answers to common questions about Velmor Spire. From reservation details to service inquiries, our FAQ section has you covered.</p>
    <div class="faq-btn">See more FAQs</div>
    <div class="faq-list">
      <div class="faq-item">
        <p class="faq-q">How can I book a meeting room at Velmor Spire Office?</p>
        <svg width="8" height="6" viewBox="0 0 8 6"><path d="M1 5 L4 2 L7 5" fill="none" stroke="#D4A02A" stroke-width="1.2"/></svg>
        <p class="faq-a">Reserving a meeting room at Velmor Spire Office is easy! Simply visit our website and navigate to the "Meeting Rooms" section. From there, you can view available rooms, select your preferred date and time, and complete the reservation online. Alternatively, you can contact our reception desk for assistance with your request.</p>
      </div>
      <div class="faq-item">
        <p class="faq-q">Are there any additional fees for using the facilities at Velmor Spire Residence?</p>
        <svg width="8" height="6" viewBox="0 0 8 6"><path d="M1 1 L4 4 L7 1" fill="none" stroke="#D4A02A" stroke-width="1.2"/></svg>
      </div>
      <div class="faq-item">
        <p class="faq-q">What safety measures are in place at Velmor Spire Office in response to COVID-19?</p>
        <svg width="8" height="6" viewBox="0 0 8 6"><path d="M1 1 L4 4 L7 1" fill="none" stroke="#D4A02A" stroke-width="1.2"/></svg>
      </div>
    </div>
    <div class="connect" role="img" aria-label="Lounge interior in warm dark tones behind the contact section">
      <h2>Let's Connect</h2>
      <p>Have questions or ready to start your journey with us? Get in touch with our team today by filling out the form below. Whether you're interested in touring the space, requesting a quote, or simply want more information, we're here to assist you every step of the way.</p>
      <div class="cta">Get in Touch</div>
    </div>
  </section>
</body>
</html>
```